Varnik Holdings — Business Card Design Brief
Overview
Design a double-sided business card for Varnik Holdings that highlights our two service arms: Varnik Communications (telecommunications) and Varnik Energy (business energy solutions). The card should feel smart and stand out when handed to clients.

Objectives
Showcase our areas of specialty clearly.
Reflect the overall Varnik / Varnik Holdings brand while acknowledging both arms.
Explore using both logos (Communications + Energy) or one unified logo, depending on the design.

Deliverables
One double-sided business card design (front + back).

Content & Copy
Front (preferred): Logo: Varnik / Varnik Holdings
Descriptor: Business Communications | Business Energy
Back:My contact details and company details
Core products: Business Mobile • Telephony • Internet • Business Energy Solutions

Brand & Visual Direction
We have a group logo currently tailored more toward telecoms, plus a separate Varnik Energy logo.
Please explore layouts that use both logos or just one, whichever works best.
Color: I wouldn't mind seeing an option using our the Blue/Purple gradient from our website (varnik-example.co.uk), but also open to non-gradient approaches and other colours..

Overall look: Smart, modern, and distinctive.
Format & Print Specs
Double-sided business card format. (Use a standard size

Must-Haves
Front: Varnik wording or Varnik Holdings wording with atleast 1 logo also on front “Business Communications | Business Energy.”

Back: Contact + company details and core products.
A design that stands out while remaining professional.

Nice-to-Have Options
A gradient version using our site’s Blue/Purple gradient.
A non-gradient version.
A dual-logo treatment versus a single-logo treatment.

Thanks
Owen

```html
<!DOCTYPE html>
<html lang="en">
<head>
<meta charset="utf-8">
<title>Varnik Holdings — Business Card</title>
<link rel="stylesheet" href="https://fonts.googleapis.com/css2?family=Poppins:wght@400;500;600;700&display=swap">
<style>
  :root {
    --backdrop: #d4d5d8;
    --navy: #282259;
    --ink: #2a2260;
    --text: #222222;
    --white: #ffffff;
    --cream: #fdfaf2;
    --comms-blue: #3a5cc4;
    --energy-green: #3aa63c;
    --accent-purple: #8a3a8a;
  }
  * { margin: 0; padding: 0; box-sizing: border-box; }
  html, body {
    width: 900px; height: 1200px; overflow: hidden;
    background: var(--backdrop);
    font-family: "Poppins", sans-serif;
  }
  .canvas { position: relative; width: 900px; height: 1200px; }

  /* Front */
  .card-front {
    position: absolute; left: 149px; top: 168px;
    width: 601px; height: 386px;
    background: var(--navy);
  }
  .brand { position: absolute; top: 0; }
  .brand--comms { left: 46px; }
  .brand--energy { left: 324px; }
  .brand-mark { position: absolute; top: 93px; }
  .brand--comms .brand-mark { left: 4px; }
  .brand--energy .brand-mark { left: -6px; }
  .brand-name {
    position: absolute; left: 0; top: 208px;
    font-weight: 700; font-size: 62px; line-height: 1;
    color: var(--white); letter-spacing: 0.5px;
    white-space: nowrap;
  }
  .brand-descriptor {
    position: absolute; left: 2px; top: 280px;
    font-weight: 500; font-size: 15px; letter-spacing: 1.2px;
    color: var(--white); white-space: nowrap;
  }

  /* Back */
  .card-back {
    position: absolute; left: 149px; top: 644px;
    width: 602px; height: 388px;
    background: var(--cream);
  }
  .card-back__panel {
    position: absolute; left: 22px; top: 143px; right: 0; bottom: 0;
    background: var(--white);
  }
  .holder {
    position: absolute; right: 331px; top: 167px; text-align: right;
  }
  .holder__name {
    font-weight: 600; font-size: 25px; line-height: 1.1; color: var(--ink);
    white-space: nowrap;
  }
  .holder__role {
    font-size: 14px; letter-spacing: 0.6px; color: var(--text); margin-top: 1px;
  }
  .divider {
    position: absolute; left: 297px; top: 164px;
    width: 2px; height: 60px; background: var(--ink);
  }
  .contact { position: absolute; left: 319px; top: 160px; list-style: none; }
  .contact__item {
    display: flex; align-items: center; gap: 4px;
    font-size: 15px; letter-spacing: 1.1px; color: var(--text);
    height: 22px; white-space: nowrap;
  }
  .contact__icon { width: 12px; height: 12px; flex: none; }
  .address {
    position: absolute; left: 0; right: 0; top: 274px;
    text-align: center; font-size: 14px; color: var(--text); letter-spacing: 0.2px;
  }
  .products {
    position: absolute; left: 0; right: 0; top: 325px;
    text-align: center; font-weight: 600; font-size: 15px; color: var(--ink);
    letter-spacing: 0.3px; white-space: nowrap;
  }
</style>
</head>
<body>
<div class="canvas">

  <section class="card-front" aria-label="Business card front">
    <div class="brand brand--comms">
      <svg class="brand-mark" width="116" height="116" viewBox="0 0 116 116" aria-hidden="true">
        <circle cx="58" cy="58" r="52" fill="none" stroke="var(--comms-blue)" stroke-width="8"/>
      </svg>
      <div class="brand-name">VARNIK</div>
      <div class="brand-descriptor">Business Communications</div>
    </div>
    <div class="brand brand--energy">
      <svg class="brand-mark" width="116" height="116" viewBox="0 0 116 116" aria-hidden="true">
        <circle cx="58" cy="58" r="52" fill="none" stroke="var(--energy-green)" stroke-width="8"/>
      </svg>
      <div class="brand-name">VARNIK</div>
      <div class="brand-descriptor">Business Energy</div>
    </div>
  </section>

  <section class="card-back" aria-label="Business card back">
    <div class="card-back__panel"></div>

    <div class="holder">
      <div class="holder__name">Lukas Brenner</div>
      <div class="holder__role">Geschäftsführer</div>
    </div>
    <div class="divider"></div>

    <ul class="contact">
      <li class="contact__item">
        <svg class="contact__icon" viewBox="0 0 24 24" aria-hidden="true"><path fill="var(--accent-purple)" d="M6.6 10.8a15 15 0 0 0 6.6 6.6l2.2-2.2a1 1 0 0 1 1-.25 11.4 11.4 0 0 0 3.6.57 1 1 0 0 1 1 1V20a1 1 0 0 1-1 1A17 17 0 0 1 3 4a1 1 0 0 1 1-1h3.5a1 1 0 0 1 1 1c0 1.25.2 2.45.57 3.57a1 1 0 0 1-.25 1z"/></svg>
        +44 0161 496 0123
      </li>
      <li class="contact__item">
        <svg class="contact__icon" viewBox="0 0 24 24" aria-hidden="true"><rect x="2" y="5" width="20" height="14" fill="var(--accent-purple)"/><path d="M2 5l10 8 10-8" fill="none" stroke="#fff" stroke-width="1.6"/></svg>
        info@varnik-example.co.uk
      </li>
      <li class="contact__item">
        <svg class="contact__icon" viewBox="0 0 24 24" aria-hidden="true"><g fill="none" stroke="var(--accent-purple)" stroke-width="2"><circle cx="12" cy="12" r="9.5"/><ellipse cx="12" cy="12" rx="4.5" ry="9.5"/><path d="M2.5 12h19M4 7h16M4 17h16"/></g></svg>
        varnik-example.co.uk
      </li>
    </ul>

    <p class="address">24 Alder Row, Manchester, England, M1 7QT</p>
    <p class="products">Business Mobile • Telephony • Internet • Business Energy Solutions</p>
  </section>

</div>
</body>
</html>
```